Velk Partners Building Business Cards

We need a business card that reflects our business as "Solar Experts" in San Diego. Browse our website www.velkpartners.example our License needs to be displayed as "CSLB# 3867140" our phone number is (619) 555-0187

Save thousands on your electric bills and increase the value of your home while helping to protect the environment. Our solar installation experts will help you design the system that's right for you, using only the highest quality equipment that will look great and give you ideal performance. Our goal is to make you energy independent, and get your electric bill to 0.

Paul Osterby
(619) 555-0187
paul@velkpartners.example

Target Market(s)

Home owners in san diego looking for solar

Industry/Entity Type

Solar Energy

Contact Information for Business Card

Paul Osterby
(619) 555-0187
paul@velkpartners.example

Font styles to use
Other font styles liked:
• Use our logo font

Requirements
Must have
• License needs to be displayed as "CSLB# 3867140" our phone number is (619) 555-0187
Nice to have
• Real images of rooftop home solar in san diego
Should not have
• our business address

```html
<!DOCTYPE html>
<html lang="en">
<head>
<meta charset="utf-8">
<title>Velk Partners Building – Business Card</title>
<link rel="stylesheet" href="https://fonts.googleapis.com/css2?family=Source+Sans+3:wght@400;600;800&display=swap">
<style>
  :root {
    --navy: #1f3f7f;
    --sun: #f5a90f;
    --paper: #ffffff;
    --backdrop: #e9e6e1;
    --shadow: rgba(20, 30, 50, 0.25);
  }
  * { box-sizing: border-box; margin: 0; padding: 0; }
  html, body {
    width: 1200px; height: 950px; overflow: hidden;
    background: var(--backdrop);
    font-family: "Source Sans 3", "Myriad Pro", Arial, sans-serif;
  }
  .stage { position: relative; width: 1200px; height: 950px; }
  .card {
    position: absolute; left: 250px; width: 700px; height: 400px;
    box-shadow: 0 10px 30px var(--shadow);
    overflow: hidden;
  }
  .card--front { top: 50px; background: var(--navy); }
  .card--back { top: 500px; background: var(--navy); }

  .card__art { position: absolute; inset: 0; }

  .brand {
    position: absolute; left: 56px; top: 96px;
    display: flex; align-items: center; gap: 14px;
    color: var(--navy); font-weight: 800;
  }
  .brand__dot { width: 32px; height: 32px; border-radius: 50%; background: var(--sun); flex: none; }
  .brand__name { font-size: 42px; line-height: 1; letter-spacing: -0.5px; }

  .holder {
    position: absolute; left: 40px; bottom: 26px; color: var(--paper);
    font-size: 17px; line-height: 1.3;
  }
  .holder__name { color: var(--sun); font-weight: 800; font-size: 22px; }

  .contact {
    position: absolute; right: 28px; top: 56px; list-style: none;
    color: var(--paper); font-size: 16px;
  }
  .contact__item {
    display: flex; align-items: center; justify-content: flex-end; gap: 10px;
    height: 28px; white-space: nowrap;
  }
  .contact__icon { width: 16px; height: 16px; flex: none; }

  .back-mark {
    position: absolute; right: 60px; bottom: 60px;
    display: flex; flex-direction: column; align-items: flex-end; gap: 10px;
    color: var(--paper);
  }
  .back-mark__brand { display: flex; align-items: center; gap: 12px; font-weight: 800; font-size: 26px; }
  .back-mark__dot { width: 26px; height: 26px; border-radius: 50%; background: var(--sun); }
  .back-mark__web { font-size: 16px; }
</style>
</head>
<body>
<main class="stage">

  <section class="card card--front" aria-label="Business card front">
    <svg class="card__art" viewBox="0 0 700 400" width="700" height="400" aria-hidden="true">
      <rect width="700" height="400" fill="var(--navy)"/>
      <polygon points="0,0 420,0 380,238 0,290" fill="var(--paper)"/>
      <polygon points="420,0 434,0 392,250 0,304 0,290 380,238" fill="var(--sun)"/>
    </svg>

    <div class="brand">
      <span class="brand__dot"></span>
      <span class="brand__name">Velk Partners<br>Building</span>
    </div>

    <div class="holder">
      <p class="holder__name">Paul Osterby</p>
      <p>CEO/Founder</p>
      <p>CSLB# 3867140</p>
    </div>

    <ul class="contact">
      <li class="contact__item">(619) 555-0187
        <svg class="contact__icon" viewBox="0 0 16 16"><circle cx="8" cy="8" r="8" fill="var(--sun)"/><path d="M5 4l2 .4.4 2-1 .8a5 5 0 0 0 2.4 2.4l.8-1 2 .4.4 2c-3.5.6-7.6-3.5-7-7z" fill="var(--navy)"/></svg>
      </li>
      <li class="contact__item">paul@velkpartners.example
        <svg class="contact__icon" viewBox="0 0 16 16"><circle cx="8" cy="8" r="8" fill="var(--sun)"/><rect x="4" y="5" width="8" height="6" fill="var(--navy)"/><path d="M4 5l4 3.2L12 5" stroke="var(--sun)" fill="none"/></svg>
      </li>
      <li class="contact__item">www.velkpartners.example
        <svg class="contact__icon" viewBox="0 0 16 16"><circle cx="8" cy="8" r="8" fill="var(--sun)"/><circle cx="8" cy="8" r="4.5" stroke="var(--navy)" stroke-width="1.3" fill="none"/><path d="M3.5 8h9M8 3.5c-2 2.5-2 6.5 0 9M8 3.5c2 2.5 2 6.5 0 9" stroke="var(--navy)" stroke-width="1" fill="none"/></svg>
      </li>
    </ul>
  </section>

  <section class="card card--back" aria-label="Business card back">
    <div class="back-mark">
      <div class="back-mark__brand"><span class="back-mark__dot"></span>Velk Partners Building</div>
      <p class="back-mark__web">www.velkpartners.example</p>
    </div>
  </section>

</main>
</body>
</html>
```